NEW Modern Sleek Business Card for VR Language Startup

Our startup is using VR to lead the next wave of world language education. We need a two-sided business card that introduces the larger organization (Brightloom Language Inc) and our contact info on one side and shows the product, Glimwoorld, on the other side.

Side 1 (contact info)= Brightloom Logo and Contact info (name, title, phone, email)

Side 2 (product)= Glimworld logo, text, and website
Text= Culturally Immersive Language Learning Games
Website= www.glimworld-play.com

Target Market(s)

Education, Technology

Contact Information for Business Card

Contact info will be updated upon approval of the design. For now, put this as a placeholder.

Perry Dunmore
Founder & CEO
pdunmore@quillpost-mail.net
(555)-014-2286

Font styles to use
Other font styles liked:
• Gibson and Century Gothic are the brand fonts

Requirements
Nice to have
• I would love to see cohesion between the design and colors of the two logos. I have attached a few business card designs that I like, so you can get a feel for my preferred style.

```html
<!DOCTYPE html>
<html lang="en">
<head>
<meta charset="utf-8">
<title>Brightloom Language – Business Card</title>
<link rel="stylesheet" href="https://fonts.googleapis.com/css2?family=Questrial&family=Montserrat:wght@700&display=swap">
<style>
  :root {
    --stage: #1d1e23;
    --paper: #ffffff;
    --ink: #1a1a1a;
    --ink-soft: #4a4a4a;
    --cyan: #4cc6e2;
    --violet: #7258b0;
    --orange: #f6923a;
    --red: #ee3b52;
    --magenta: #b93c8f;
    --blue: #4f73c4;
    --card-w: 600px;
    --card-h: 343px;
  }
  * { box-sizing: border-box; margin: 0; padding: 0; }
  html, body { width: 1200px; height: 800px; overflow: hidden; background: var(--stage); }
  .stage {
    width: 1200px; height: 800px;
    display: flex; flex-direction: column; align-items: center; justify-content: center; gap: 40px;
  }
  .card {
    position: relative; width: var(--card-w); height: var(--card-h);
    border-radius: 18px; overflow: hidden;
    box-shadow: 0 14px 30px rgba(0,0,0,.45);
  }

  /* Product side */
  .card--product {
    background: linear-gradient(150deg, var(--cyan) 0%, #5aa6d8 40%, var(--violet) 100%);
    color: #fff; font-family: "Questrial", sans-serif;
  }
  .product-decor {
    position: absolute; left: -70px; bottom: -90px; width: 340px; height: 300px;
    border-radius: 50%;
    background: radial-gradient(circle at 50% 50%, rgba(255,255,255,.12), rgba(255,255,255,0) 70%);
  }
  .product-brand {
    position: absolute; top: 104px; left: 0; right: 0;
    display: flex; align-items: center; justify-content: center; gap: 16px;
  }
  .brand-dot { width: 46px; height: 46px; border-radius: 50%; background: #fff; }
  .product-name { font-size: 50px; letter-spacing: .5px; line-height: 1; }
  .product-tagline { position: absolute; top: 196px; left: 0; right: 0; text-align: center; font-size: 19px; }
  .product-site { position: absolute; top: 226px; left: 0; right: 0; text-align: center; font-size: 16px; }

  /* Contact side */
  .card--contact { background: var(--paper); color: var(--ink); font-family: "Questrial", sans-serif; }
  .contact-decor {
    position: absolute; right: -120px; top: -200px; width: 560px; height: 420px;
    border-radius: 50%;
    background: linear-gradient(125deg, var(--orange) 0%, var(--red) 38%, var(--magenta) 68%, var(--blue) 100%);
  }
  .company-brand {
    position: absolute; left: 40px; top: 118px;
    display: flex; align-items: center; gap: 14px;
  }
  .company-dot {
    width: 52px; height: 52px; border-radius: 50%;
    background: linear-gradient(135deg, var(--orange), var(--red) 45%, var(--magenta) 75%, var(--cyan));
  }
  .company-name { font-size: 30px; color: var(--ink); letter-spacing: 1px; line-height: 1; }
  .person-name {
    position: absolute; left: 40px; top: 214px;
    font-family: "Montserrat", sans-serif; font-weight: 700; font-size: 17px; letter-spacing: .3px;
  }
  .person-title { position: absolute; left: 40px; top: 238px; font-size: 15px; color: var(--ink-soft); }
  .contact-list { position: absolute; left: 40px; top: 270px; list-style: none; }
  .contact-item { display: flex; align-items: center; gap: 9px; font-size: 14px; color: var(--ink-soft); margin-bottom: 8px; }
  .contact-icon {
    width: 20px; height: 20px; border-radius: 50%;
    background: linear-gradient(135deg, var(--red), var(--magenta));
    display: flex; align-items: center; justify-content: center;
  }
</style>
</head>
<body>
<main class="stage">
  <section class="card card--product" aria-label="Product side">
    <div class="product-decor" role="img" aria-label="Faint product emblem decoration"></div>
    <div class="product-brand">
      <span class="brand-dot"></span>
      <span class="product-name">Glimworld</span>
    </div>
    <p class="product-tagline">Culturally Immersive Language Learning Games</p>
    <p class="product-site">www.glimworld-play.com</p>
  </section>

  <section class="card card--contact" aria-label="Contact side">
    <div class="contact-decor" role="img" aria-label="Large colourful company emblem artwork"></div>
    <div class="company-brand">
      <span class="company-dot"></span>
      <span class="company-name">Brightloom Language</span>
    </div>
    <p class="person-name">PERRY DUNMORE</p>
    <p class="person-title">Founder &amp; CEO</p>
    <ul class="contact-list">
      <li class="contact-item">
        <span class="contact-icon">
          <svg width="11" height="11" viewBox="0 0 24 24" aria-hidden="true"><path fill="#fff" d="M6.6 10.8a15 15 0 0 0 6.6 6.6l2.2-2.2c.3-.3.7-.4 1-.2 1.1.4 2.3.6 3.6.6.6 0 1 .4 1 1V20c0 .6-.4 1-1 1A17 17 0 0 1 3 4c0-.6.4-1 1-1h3.5c.6 0 1 .4 1 1 0 1.3.2 2.5.6 3.6.1.3 0 .7-.2 1z"/></svg>
        </span>
        (555)-014-2286
      </li>
      <li class="contact-item">
        <span class="contact-icon">
          <svg width="11" height="11" viewBox="0 0 24 24" aria-hidden="true"><path fill="#fff" d="M3 5h18v14H3z"/><path fill="none" stroke="#c0407a" stroke-width="2" d="M3 6l9 7 9-7"/></svg>
        </span>
        pdunmore@quillpost-mail.net
      </li>
    </ul>
  </section>
</main>
</body>
</html>
```